Dalvick's Business Card

I need some designs for a new business card including the new logo attached. An old example of our business card is also attached to show all the data that should be included on the new design.
**I added some more examples someone had mocked up**

Contact Information for Business Card

Should include all info on other examples uploaded.

```html
<!DOCTYPE html>
<html lang="en">
<head>
<meta charset="utf-8">
<title>Dalvick's Business Card</title>
<link href="https://fonts.googleapis.com/css2?family=Montserrat:wght@400;500;700;800&display=swap" rel="stylesheet">
<style>
  :root {
    --page: #e6e6e6;
    --blue: #0a67b0;
    --blue-dark: #0757a0;
    --red: #e02630;
    --white: #f3f3f3;
    --text-light: #ffffff;
  }
  * { margin: 0; padding: 0; box-sizing: border-box; }
  html, body {
    width: 1200px; height: 1200px; overflow: hidden;
    background: var(--page);
    font-family: "Montserrat", sans-serif;
  }
  .card {
    position: absolute; left: 235px;
    width: 730px; height: 418px;
    overflow: hidden;
    box-shadow: -6px 10px 22px rgba(0,0,0,0.28);
  }
  .card--front { top: 160px; }
  .card--back { top: 632px; }
  .card__bg { position: absolute; inset: 0; width: 100%; height: 100%; }
  .card__text { position: absolute; color: var(--text-light); }
  .tagline { font-size: 22px; font-weight: 400; letter-spacing: 0.3px; }
  .tagline--top { left: 50px; top: 22px; }
  .tagline--bottom { right: 42px; top: 368px; }
  .person-name {
    position: absolute; left: 80px; top: 150px;
    font-size: 31px; font-weight: 800; color: var(--red); letter-spacing: 0.2px;
  }
  .contact { position: absolute; left: 80px; top: 220px; list-style: none; }
  .contact li {
    display: flex; align-items: center; gap: 8px;
    font-size: 22px; color: var(--blue); height: 32px;
  }
  .contact svg { width: 18px; height: 18px; flex: none; }
  .brand {
    position: absolute; display: flex; align-items: center; gap: 12px;
    font-weight: 700; color: var(--blue);
  }
  .brand__dot { border-radius: 50%; background: var(--red); flex: none; }
  .brand--front { right: 70px; top: 178px; font-size: 34px; }
  .brand--front .brand__dot { width: 26px; height: 26px; }
  .brand--back { left: 0; right: 0; justify-content: center; top: 172px; font-size: 62px; }
  .brand--back .brand__dot { width: 44px; height: 44px; }
  .service-area { left: 42px; top: 34px; font-size: 16px; line-height: 23px; letter-spacing: 0.4px; }
  .call-to-action { right: 47px; top: 353px; font-size: 16px; line-height: 23px; text-align: right; letter-spacing: 0.3px; }
  strong { font-weight: 700; }
</style>
</head>
<body>

<section class="card card--front">
  <svg class="card__bg" viewBox="0 0 1175 672" preserveAspectRatio="none" aria-hidden="true">
    <defs>
      <linearGradient id="blueFront" x1="0" y1="0" x2="1" y2="1">
        <stop offset="0" stop-color="#0757a0"/><stop offset="1" stop-color="#0e80c4"/>
      </linearGradient>
    </defs>
    <rect width="1175" height="672" fill="url(#blueFront)"/>
    <path d="M280,125 C600,60 900,45 1175,58 L1175,220 L0,320 Z" fill="var(--red)"/>
    <path d="M0,450 L0,615 C400,625 700,590 900,540 L1175,440 Z" fill="var(--red)"/>
    <path d="M0,220 C300,110 700,70 1175,150 L1175,452 C900,545 500,600 0,520 Z" fill="var(--white)"/>
  </svg>
  <p class="card__text tagline tagline--top">Family Owned &amp; Operated</p>
  <h1 class="person-name">MARK DALVICK</h1>
  <ul class="contact">
    <li>
      <svg viewBox="0 0 24 24" aria-hidden="true"><path fill="var(--red)" d="M6.6 10.8a15.1 15.1 0 0 0 6.6 6.6l2.2-2.2a1 1 0 0 1 1-.25 11.4 11.4 0 0 0 3.6.57 1 1 0 0 1 1 1V20a1 1 0 0 1-1 1A17 17 0 0 1 3 4a1 1 0 0 1 1-1h3.5a1 1 0 0 1 1 1c0 1.25.2 2.45.57 3.6a1 1 0 0 1-.25 1z"/></svg>
      555.014.2290
    </li>
    <li>
      <svg viewBox="0 0 24 24" aria-hidden="true"><path fill="var(--red)" d="M2 5h20v14H2z"/><path d="M2 6l10 7 10-7" fill="none" stroke="#fff" stroke-width="1.6"/></svg>
      hvacdalvick@mailbox.com
    </li>
  </ul>
  <div class="brand brand--front"><span class="brand__dot"></span>DALVICK'S</div>
  <p class="card__text tagline tagline--bottom">Licensed &amp; insured</p>
</section>

<section class="card card--back">
  <svg class="card__bg" viewBox="0 0 1175 672" preserveAspectRatio="none" aria-hidden="true">
    <defs>
      <linearGradient id="blueBack" x1="0" y1="0" x2="1" y2="1">
        <stop offset="0" stop-color="#0757a0"/><stop offset="1" stop-color="#0e80c4"/>
      </linearGradient>
    </defs>
    <rect width="1175" height="672" fill="url(#blueBack)"/>
    <path d="M280,185 C600,120 900,105 1175,118 L1175,280 L0,380 Z" fill="var(--red)"/>
    <path d="M0,450 L0,552 C400,562 700,530 900,478 L1175,380 Z" fill="var(--red)"/>
    <path d="M0,282 C300,170 700,130 1175,210 L1175,390 C900,480 500,540 0,460 Z" fill="var(--white)"/>
  </svg>
  <p class="card__text service-area">SERVES MAPLE RIDGE,<br>IA &amp; <strong>SURROUNDING AREAS</strong></p>
  <div class="brand brand--back"><span class="brand__dot"></span>DALVICK'S</div>
  <p class="card__text call-to-action">CALL TODAY FOR ALL YOUR <strong>HVAC,</strong><br><strong>REFRIGERATION</strong> &amp; <strong>PLUMBING NEEDS</strong></p>
</section>

</body>
</html>
```